Corporate Business Card

Very professional, Modern, Not to busy, include phone address email, website
(253) 617-4930, 18761 52nd Avenue S, Kent, WA 98047, martin@plumlinegroup.com, varkoworks.com

Target Market(s)

Manufacturing

Industry/Entity Type

Aero, machining, manufacturing, Off road racing

Contact Information for Business Card

Phone, address email, website

```html
<!DOCTYPE html>
<html lang="en">
<head>
<meta charset="utf-8">
<title>Varko Works — Business Card</title>
<link rel="stylesheet" href="https://fonts.googleapis.com/css2?family=Play:wght@400;700&display=swap">
<style>
  :root {
    --backdrop: #1b1b1c;
    --kraft-light: #dcbc8f;
    --kraft-mid: #c9a371;
    --kraft-dark: #a47947;
    --navy: #1f3a78;
    --red: #d6252e;
  }
  * { box-sizing: border-box; margin: 0; padding: 0; }
  html, body {
    width: 1093px;
    height: 1200px;
    overflow: hidden;
    background: var(--backdrop);
  }
  .stage {
    position: relative;
    width: 1093px;
    height: 1200px;
  }
  .card {
    position: absolute;
    left: 264px;
    width: 580px;
    height: 357px;
    background: radial-gradient(ellipse at 35% 5%, var(--kraft-light) 0%, var(--kraft-mid) 45%, var(--kraft-dark) 100%);
    font-family: 'Play', sans-serif;
    color: var(--navy);
    text-align: center;
  }
  .card--front { top: 226px; }
  .card--back { top: 620px; }

  .contact {
    position: absolute;
    left: 0;
    right: 0;
    top: 74px;
  }
  .contact__name {
    font-weight: 700;
    font-size: 21px;
    letter-spacing: 0.3px;
    line-height: 24px;
  }
  .contact__title {
    color: var(--red);
    font-size: 17px;
    line-height: 20px;
  }
  .contact__rule {
    width: 115px;
    height: 1px;
    background: var(--navy);
    margin: 12px auto;
  }
  .contact__line {
    font-size: 17px;
    line-height: 23px;
    letter-spacing: 0.3px;
  }

  .brand {
    position: absolute;
    left: 0;
    right: 0;
    top: 150px;
    display: flex;
    justify-content: center;
    align-items: center;
    gap: 14px;
  }
  .brand__mark {
    width: 30px;
    height: 30px;
    background: var(--red);
  }
  .brand__name {
    font-weight: 700;
    font-size: 46px;
    line-height: 54px;
    letter-spacing: 1px;
    color: var(--navy);
  }
</style>
</head>
<body>
<main class="stage">
  <section class="card card--front">
    <div class="contact">
      <p class="contact__name">DANIEL REEVES</p>
      <p class="contact__title">Managing Director</p>
      <div class="contact__rule"></div>
      <p class="contact__line">(253) 617-4930</p>
      <p class="contact__line">martin@plumlinegroup.com</p>
      <p class="contact__line">www.varkoworks.com</p>
      <div class="contact__rule"></div>
      <p class="contact__line">18761 52nd Avenue S</p>
      <p class="contact__line">Kent, WA 98047</p>
    </div>
  </section>

  <section class="card card--back">
    <div class="brand">
      <span class="brand__mark"></span>
      <span class="brand__name">VARKO WORKS</span>
    </div>
  </section>
</main>
</body>
</html>
```